Website for a high end London wedding DJ company

I want a website that is fairly basic but modern. It needs to look professional and smooth. I like white and black backgrounds. I am looking for something similar to this: https://www.torvalinsky.uk - at the bottom of this page it has ravenquill reviews as well. I mainly use bimmlo reviews. This would need to be included, or at least some way of showing all my 5 star reviews on the first page, to get peoples attention.
My current website is www.marrowandtide.com
My

1 page

• A way to display my reviews. Must be modern.
• Must not look cheesy and 8

```html
<!DOCTYPE html>
<html lang="en">
<head>
<meta charset="utf-8">
<title>Marrow &amp; Tide — London Wedding DJs</title>
<link href="https://fonts.googleapis.com/css2?family=Actor&family=Lato:ital,wght@0,400;0,700;1,400&family=Open+Sans:wght@400;700&display=swap" rel="stylesheet">
<style>
:root{
  --green:#5cb87a;
  --green-deep:#4fae6e;
  --green-band:#62bb7c;
  --star-gold:#f3c04a;
  --ink:#222;
  --text:#555;
  --white:#fff;
  --grey-bg:#f4f4f4;
  --footer:#1c1a1f;
  --hero-a:#2a1420;
  --hero-b:#7a1f3a;
}
*{box-sizing:border-box;margin:0;padding:0}
html,body{width:1200px;height:3801px;overflow:hidden}
body{position:relative;font-family:'Lato',sans-serif;color:var(--text);background:var(--white)}
.abs{position:absolute}
.heading{font-family:'Actor',sans-serif;color:var(--ink);font-weight:400;text-align:center;left:0;width:1200px}
.divider{left:467px;width:266px;height:12px}
.divider::before{content:"";position:absolute;left:0;right:0;top:5px;border-top:1.5px dotted #777}
.divider.light::before{border-color:rgba(255,255,255,.9)}

/* hero */
.hero{left:0;top:0;width:1200px;height:599px;background:radial-gradient(ellipse at 75% 30%,#8a2440 0%,var(--hero-b) 25%,var(--hero-a) 65%,#120a10 100%)}
.logo{font-family:'Actor',sans-serif;color:var(--white);font-size:32px;left:134px;top:28px;width:267px;text-align:center}
.nav{right:131px;top:40px;display:flex;gap:27px;font-family:'Open Sans',sans-serif;font-weight:700;font-size:14px;color:var(--white)}
.hero-title{top:245px;font-size:48px;color:var(--white)}
.rating{display:flex;gap:4px}
.rating svg{display:block}
.hero-rating{left:526px;top:366px}
.hero-sub{top:412px;left:0;width:1200px;text-align:center;color:var(--white);font-size:15px}
.video{left:193px;top:534px;width:805px;height:369px;background:linear-gradient(120deg,#5d8ed4 0%,#a9c7ee 45%,#f0d6ec 80%,#f7eef7 100%);box-shadow:0 12px 24px rgba(0,0,0,.35)}
.play{left:574px;top:697px;width:44px;height:44px;border-radius:50%;background:var(--white);display:flex;align-items:center;justify-content:center}

/* about */
.about-title{top:950px;font-size:35px}
.about-text{left:185px;top:1035px;width:830px;text-align:center;font-size:14.5px;line-height:28px}
.btn{display:flex;align-items:center;justify-content:center;border-radius:26px;font-size:15px;text-transform:uppercase}
.btn-solid{background:var(--green);color:var(--white)}
.btn-white{background:var(--white);color:var(--green)}
.about-btn{left:518px;top:1219px;width:164px;height:46px}

/* dj band */
.dj-band{left:0;top:1349px;width:1200px;height:794px;background:radial-gradient(ellipse at 50% 20%,#7ccb91 0%,var(--green-band) 45%,var(--green-deep) 100%)}
.dj-title{top:1410px;font-size:35px;color:var(--white)}
.card{width:296px;height:496px;top:1514px;border-radius:8px}
.card-head{left:0;top:0;width:100%;height:276px;background:var(--white);border-radius:8px}
.card.full{background:var(--white)}
.card-name{top:12px;left:0;width:100%;text-align:center;font-family:'Actor',sans-serif;font-size:24px;color:var(--ink)}
.card-photo{left:4px;top:52px;width:288px;height:217px;border-radius:6px}
.card-text{left:18px;top:284px;width:260px;text-align:center;font-size:13.5px;line-height:24px;color:var(--white)}
.card.full .card-text{color:var(--text)}
.card-btn{left:66px;top:428px;width:164px;height:45px}
.book-line{top:2044px;left:0;width:1200px;text-align:center;color:var(--white);font-size:15px}
.book-line span{text-decoration:underline}

/* reviews */
.rev-title{top:2214px;font-size:35px}
.rev-rating{left:538px;top:2345px}
.rev-text{left:215px;top:2380px;width:770px;text-align:center;font-style:italic;font-size:14.5px;line-height:28px;color:#555}
.arrow{top:2398px;width:20px;height:40px}

/* gallery */
.gallery-bg{left:0;top:2568px;width:1200px;height:856px;background:var(--grey-bg)}
.gal-title{top:2640px;font-size:35px}
.insta-btn{left:460px;top:2740px;width:280px;height:47px;border:1.5px solid #444;border-radius:26px;display:flex;align-items:center;justify-content:center;gap:10px;font-size:15px;color:#333}
.insta-btn i{width:14px;height:14px;border:2px solid #333;border-radius:3px}
.tile{position:absolute}

/* footer */
.footer{left:0;top:3424px;width:1200px;height:377px;background:radial-gradient(ellipse at 50% 0%,#3a2e38 0%,var(--footer) 60%,#0f0e11 100%)}
.foot-logo{left:134px;top:3534px;width:229px;font-size:28px}
.social{top:3600px;width:30px;height:30px;border-radius:50%;background:var(--green)}
.foot-col{top:3494px;color:var(--white);font-size:13px}
.foot-col h4{font-weight:400;font-size:15px;margin-bottom:14px;text-transform:uppercase}
.foot-col li{list-style:none;line-height:28px}
.news p{width:260px;line-height:28px}
.email{left:800px;top:3597px;width:267px;height:41px;background:var(--white);border-radius:21px;font-size:12px;color:#888;padding:13px 0 0 12px}
.send{left:1033px;top:3609px}
.foot-rule{left:103px;top:3708px;width:995px;border-top:1px solid rgba(255,255,255,.4)}
.copy{left:0;top:3729px;width:1200px;text-align:center;color:var(--white);font-size:12.5px}
</style>
</head>
<body>

<!-- hero -->
<div class="abs hero" role="img" aria-label="DJ mixing desk and headphones lit in red and pink"></div>
<div class="abs logo">Marrow &amp; Tide</div>
<nav class="abs nav"><span>HOME</span><span>DJs</span><span>REVIEWS</span><span>GALLERY</span><span>PRICES</span><span>ABOUT</span><span>EVENT PLANNER</span></nav>
<div class="abs divider light" style="top:218px" role="img" aria-label="decorative flourish"></div>
<h1 class="abs heading hero-title">WELCOME TO MARROW &amp; TIDE</h1>
<div class="abs divider light" style="top:322px" role="img" aria-label="decorative flourish"></div>
<div class="abs rating hero-rating" role="img" aria-label="Five star rating">
  <svg width="28" height="28" viewBox="0 0 24 24"><path fill="var(--star-gold)" d="M12 2l2.9 6.9 7.1.6-5.4 4.7 1.7 7-6.3-3.9-6.3 3.9 1.7-7L2 9.5l7.1-.6z"/></svg>
  <svg width="28" height="28" viewBox="0 0 24 24"><path fill="var(--star-gold)" d="M12 2l2.9 6.9 7.1.6-5.4 4.7 1.7 7-6.3-3.9-6.3 3.9 1.7-7L2 9.5l7.1-.6z"/></svg>
  <svg width="28" height="28" viewBox="0 0 24 24"><path fill="var(--star-gold)" d="M12 2l2.9 6.9 7.1.6-5.4 4.7 1.7 7-6.3-3.9-6.3 3.9 1.7-7L2 9.5l7.1-.6z"/></svg>
  <svg width="28" height="28" viewBox="0 0 24 24"><path fill="var(--star-gold)" d="M12 2l2.9 6.9 7.1.6-5.4 4.7 1.7 7-6.3-3.9-6.3 3.9 1.7-7L2 9.5l7.1-.6z"/></svg>
  <svg width="28" height="28" viewBox="0 0 24 24"><path fill="var(--star-gold)" d="M12 2l2.9 6.9 7.1.6-5.4 4.7 1.7 7-6.3-3.9-6.3 3.9 1.7-7L2 9.5l7.1-.6z"/></svg>
</div>
<p class="abs hero-sub">Ravenquill Review 5 out of 5 Reviews</p>
<div class="abs video" role="img" aria-label="Video still: DJ in headphones pointing to the sky above a festival crowd"></div>
<div class="abs play"><svg width="20" height="20" viewBox="0 0 20 20"><path d="M6 3l11 7-11 7z" fill="#1d3f7a"/></svg></div>

<!-- about -->
<h2 class="abs heading about-title">About Marrow and Tide</h2>
<div class="abs divider" style="top:1005px" role="img" aria-label="decorative flourish"></div>
<p class="abs about-text">Growing up in a big family, parties were a regular occurrence. Nights spent with loved ones full of dancing, fizz and laughter were some of our very first and very best memories. Our adoration for these happy occasions full of love and music sparked our drive to create this company. With Dean’s years of DJing experience, music has always been a big part of our life. We understand the importance of putting the music for your wedding day in the hands of the right people – people who you can trust, who understand the ins and outs of planning a wedding, who have skill, experience and a vast knowledge of music. Marrow and Tide will provide a five star, unforgettable experience.</p>
<div class="abs btn btn-solid about-btn">Learn More</div>

<!-- dj profiles -->
<section class="abs dj-band" role="img" aria-label="Blurred green-tinted dance floor lights"></section>
<h2 class="abs heading dj-title">DJ Profiles</h2>
<div class="abs divider light" style="top:1466px" role="img" aria-label="decorative flourish"></div>

<div class="abs card" style="left:131px">
  <div class="abs card-head"></div>
  <div class="abs card-name">DEAN</div>
  <div class="abs card-photo" role="img" aria-label="DJ behind a bar-style booth with purple uplighting" style="background:linear-gradient(180deg,#3a2a2a,#5a3550 60%,#b14cc9)"></div>
  <p class="abs card-text">Dean is the owner/director of Marrow and Tide and has been DJing since his mid teens. Now in his early 30s he has a wealth of DJing experience spanning close to 16 years.</p>
  <div class="abs btn btn-white card-btn">Learn More</div>
</div>

<div class="abs card full" style="left:453px">
  <div class="abs card-name">REMY</div>
  <div class="abs card-photo" role="img" aria-label="DJ in a black t-shirt standing by a doorway" style="background:linear-gradient(120deg,#ece7e2,#d9d1c8 55%,#b8aca0)"></div>
  <p class="abs card-text">Starting at just eighteen years old Remy Calder has 13 years experience as a professional DJ, with 8 of those being full time. Having held many residencies in London.</p>
  <div class="abs btn btn-solid card-btn">Learn More</div>
</div>

<div class="abs card" style="left:773px">
  <div class="abs card-head"></div>
  <div class="abs card-name">OWEN HALE</div>
  <div class="abs card-photo" role="img" aria-label="DJ in a hoodie at decks under red stage light" style="background:radial-gradient(ellipse at 50% 40%,#b01a2e,#5a0c18 60%,#1a0508)"></div>
  <p class="abs card-text">Owen is an open format DJ who is experienced in DJ’ing in great venues across the UK such as: Lantern, Copper Fox, Velvet Rooms, Orbit, Gilded Olive, Jug &amp; Fiddle and many more.</p>
  <div class="abs btn btn-white card-btn">Learn More</div>
</div>

<p class="abs book-line">To book any of the Marrow and Tide DJs email us now, or fill in the <span>contact form!</span></p>

<!-- reviews -->
<h2 class="abs heading rev-title">Reviews From Ravenquill</h2>
<div class="abs divider" style="top:2270px" role="img" aria-label="decorative flourish"></div>
<div class="abs rating rev-rating" role="img" aria-label="Five star rating">
  <svg width="24" height="24" viewBox="0 0 24 24"><path fill="var(--star-gold)" d="M12 2l2.9 6.9 7.1.6-5.4 4.7 1.7 7-6.3-3.9-6.3 3.9 1.7-7L2 9.5l7.1-.6z"/></svg>
  <svg width="24" height="24" viewBox="0 0 24 24"><path fill="var(--star-gold)" d="M12 2l2.9 6.9 7.1.6-5.4 4.7 1.7 7-6.3-3.9-6.3 3.9 1.7-7L2 9.5l7.1-.6z"/></svg>
  <svg width="24" height="24" viewBox="0 0 24 24"><path fill="var(--star-gold)" d="M12 2l2.9 6.9 7.1.6-5.4 4.7 1.7 7-6.3-3.9-6.3 3.9 1.7-7L2 9.5l7.1-.6z"/></svg>
  <svg width="24" height="24" viewBox="0 0 24 24"><path fill="var(--star-gold)" d="M12 2l2.9 6.9 7.1.6-5.4 4.7 1.7 7-6.3-3.9-6.3 3.9 1.7-7L2 9.5l7.1-.6z"/></svg>
  <svg width="24" height="24" viewBox="0 0 24 24"><path fill="var(--star-gold)" d="M12 2l2.9 6.9 7.1.6-5.4 4.7 1.7 7-6.3-3.9-6.3 3.9 1.7-7L2 9.5l7.1-.6z"/></svg>
</div>
<p class="abs rev-text">Lorem ipsum dolor sit amet, consectetur adipiscing elit, sed do eiusmod tempor incididunt ut labore et dolore magna aliqua. Quis ipsum suspendisse ultrices gravida. Risus commodo viverra maecenas accumsan lacus vel facilisis. Lorem ipsum dolor sit amet, consectetur adipiscing elit, sed do eiusmod tempor incididunt ut labore et dolore magna aliqua. Ut enim ad minim veniam, quis nostrud exercitation ut aliquip ex ea commodo consequat.</p>
<svg class="abs arrow" style="left:154px" viewBox="0 0 20 40"><path d="M15 3L5 20l10 17" fill="none" stroke="#333" stroke-width="2.5"/></svg>
<svg class="abs arrow" style="left:1026px" viewBox="0 0 20 40"><path d="M5 3l10 17L5 37" fill="none" stroke="#333" stroke-width="2.5"/></svg>

<!-- gallery -->
<section class="abs gallery-bg"></section>
<h2 class="abs heading gal-title">Our Gallery</h2>
<div class="abs divider" style="top:2695px" role="img" aria-label="decorative flourish"></div>
<div class="abs insta-btn"><i></i>FOLLOW US ON PICTURELLE</div>
<div class="tile" style="left:140px;top:2822px;width:304px;height:328px;background:linear-gradient(160deg,#3a2530,#6b3a5a 55%,#c04fd0)" role="img" aria-label="Guests dancing beside the DJ decks under purple light"></div>
<div class="tile" style="left:448px;top:2822px;width:304px;height:162px;background:linear-gradient(180deg,#3a2a2a,#5a3550 60%,#b14cc9)" role="img" aria-label="DJ booth in a bar with purple uplights"></div>
<div class="tile" style="left:756px;top:2822px;width:304px;height:162px;background:linear-gradient(180deg,#6a5a4a,#cfc6bc 60%,#efeae5)" role="img" aria-label="Brides in white dresses sharing popcorn"></div>
<div class="tile" style="left:448px;top:2988px;width:304px;height:162px;background:linear-gradient(180deg,#2a5a8a,#1e3f5c 55%,#1a1f2a)" role="img" aria-label="Wedding venue dance floor with tall windows"></div>
<div class="tile" style="left:756px;top:2988px;width:304px;height:326px;background:linear-gradient(180deg,#2c2a2a,#5a5552 50%,#9a948f)" role="img" aria-label="Black and white shot of a bride on the dance floor"></div>
<div class="tile" style="left:140px;top:3154px;width:304px;height:160px;background:linear-gradient(170deg,#5a4a40,#b88ab0 55%,#d6b6dc)" role="img" aria-label="Wedding guests celebrating in a rustic barn"></div>
<div class="tile" style="left:448px;top:3154px;width:304px;height:160px;background:linear-gradient(170deg,#4a3aa0,#6a3a8a 55%,#2a1a3a)" role="img" aria-label="Groomsmen lifting a friend on the dance floor"></div>

<!-- footer -->
<footer class="abs footer" role="img" aria-label="Dark blurred DJ equipment backdrop"></footer>
<div class="abs logo foot-logo">Marrow &amp; Tide</div>
<span class="abs social" style="left:174px" aria-label="social link"></span>
<span class="abs social" style="left:214px" aria-label="social link"></span>
<span class="abs social" style="left:254px" aria-label="social link"></span>
<span class="abs social" style="left:293px" aria-label="social link"></span>
<div class="abs foot-col" style="left:393px"><h4>Quick Menu</h4><ul><li>Home</li><li>Djs</li><li>Reviews</li><li>Gallery</li><li>Prices</li><li>Event Planner</li></ul></div>
<div class="abs foot-col" style="left:585px"><h4>Important</h4><ul><li>Terms Of Use</li><li>Privacy Policy</li><li>About Us</li><li>Contact Us</li></ul></div>
<div class="abs foot-col news" style="left:800px"><h4>Newsletter</h4><p>Lorem ipsum dolor sit amet, consectetur adipiscing elit sed do.</p></div>
<div class="abs email">Enter The Email</div>
<svg class="abs send" width="18" height="18" viewBox="0 0 24 24"><path d="M2 12L22 3l-6 19-4-8z" fill="var(--green)"/></svg>
<div class="abs foot-rule"></div>
<p class="abs copy">© Copyright 2021 &nbsp;MARROW &amp; TIDE &nbsp;&nbsp; | &nbsp;&nbsp; All Rights Reserved</p>

</body>
</html>
```